LLC needs a business card design that emphasizes consulting and expert witness in upstream oil and g

I need a business card design for my company called Obena Consultative Service, LLC. My expertise is in oil and gas upstream operations management to optimize performance and also as an expert witness for law firms in oil and gas upstream operations litigation.
The final design should communicate knowledge and hands-on experience as well as trust. (Obena means rope or lasso. Perhaps "Obena" should be in the form of a rope.) I do not like the color green in any shade. My first preference would be some shade of blue.
Industry/Entity Type
Oil And Gas

```html
<!DOCTYPE html>
<html lang="en">
<head>
<meta charset="utf-8">
<title>Obena Consultative Service – Business Card</title>
<link href="https://fonts.googleapis.com/css2?family=Roboto:wght@400&display=swap" rel="stylesheet">
<style>
  :root {
    --brand-blue: #2b3f80;
    --accent-orange: #e8621f;
    --paper: #ffffff;
    --backdrop: #e9e9ec;
  }
  html, body {
    margin: 0;
    width: 1200px;
    height: 862px;
    overflow: hidden;
    background: var(--backdrop);
  }
  .canvas {
    position: relative;
    width: 1200px;
    height: 862px;
    display: flex;
    justify-content: center;
    align-items: center;
    gap: 80px;
  }
  .card {
    position: relative;
    width: 360px;
    height: 630px;
    background: var(--paper);
    box-shadow: 0 6px 20px rgba(0,0,0,0.15);
    overflow: hidden;
    font-family: "Roboto", Arial, sans-serif;
  }
  .card-shapes {
    position: absolute;
    inset: 0;
    width: 100%;
    height: 100%;
  }
  .brand-name {
    position: absolute;
    left: 0;
    right: 0;
    margin: 0 auto;
    text-align: center;
    color: var(--brand-blue);
    font-weight: 400;
    line-height: 1.2;
  }
  .front .brand-name {
    top: 140px;
    max-width: 270px;
    font-size: 24px;
  }
  .back .brand-name {
    top: 226px;
    max-width: 300px;
    font-size: 32px;
  }
  .person {
    position: absolute;
    top: 292px;
    left: 0;
    right: 0;
    text-align: center;
    color: var(--paper);
  }
  .person-name { font-size: 25px; margin: 0; font-weight: 400; }
  .person-title { font-size: 12.5px; margin: 6px 0 0; }
  .pointer {
    position: absolute;
    top: 414px;
    left: 162px;
  }
  .contact {
    position: absolute;
    top: 470px;
    left: 0;
    right: 0;
    text-align: center;
    color: var(--paper);
    font-size: 15px;
    line-height: 1.3;
    margin: 0;
    font-style: normal;
  }
  .back-web {
    position: absolute;
    top: 532px;
    left: 0;
    right: 0;
    text-align: center;
    color: var(--paper);
    font-size: 16px;
  }
  .back-rule {
    position: absolute;
    top: 570px;
    left: 160px;
    width: 40px;
    height: 3px;
    background: var(--paper);
  }
</style>
</head>
<body>
<main class="canvas">
  <section class="card front" aria-label="Card front">
    <svg class="card-shapes" viewBox="0 0 360 630" aria-hidden="true">
      <polygon points="0,0 360,0 360,80 175,126 0,62" fill="var(--brand-blue)"/>
      <polyline points="60,83.9 175,126 320,90" fill="none" stroke="var(--accent-orange)" stroke-width="4"/>
      <polygon points="0,226 200,198 360,268 360,630 0,630" fill="var(--brand-blue)"/>
      <polyline points="60,217.6 200,198 330,254.9" fill="none" stroke="var(--accent-orange)" stroke-width="4"/>
    </svg>
    <p class="brand-name">Obena Consultative Service, LLC</p>
    <div class="person">
      <h1 class="person-name">Employee name</h1>
      <p class="person-title">Managing Director</p>
    </div>
    <svg class="pointer" width="36" height="14" viewBox="0 0 36 14" aria-hidden="true">
      <polygon points="0,0 36,0 18,12" fill="var(--paper)"/>
    </svg>
    <address class="contact">
      P : 555-0142 7310<br>
      C : 555-0198 2264<br>
      hello@obenaconsult.com<br>
      www.obenaconsult.com<br>
      418 Meridian Lane Suite 2 Harlow,<br>
      TX 77001
    </address>
  </section>

  <section class="card back" aria-label="Card back">
    <svg class="card-shapes" viewBox="0 0 360 630" aria-hidden="true">
      <polygon points="0,502 200,480 360,556 360,630 0,630" fill="var(--brand-blue)"/>
      <polyline points="60,495.4 200,480 340,546.5" fill="none" stroke="var(--accent-orange)" stroke-width="4"/>
    </svg>
    <p class="brand-name">Obena Consultative Service, LLC</p>
    <div class="back-web">www.obenaconsult.com</div>
    <div class="back-rule"></div>
  </section>
</main>
</body>
</html>
```